TA BRAMLEY BUSINESS CARD DESIGN PROJECT

We need to utilize our logo that was expertly created on PixelHarbor and now need to match this with a business card design.

```html
<!DOCTYPE html>
<html lang="en">
<head>
<meta charset="UTF-8">
<title>TA BRAMLEY Business Card</title>
<link rel="stylesheet" href="https://fonts.googleapis.com/css2?family=Open+Sans:wght@400;600;700&display=swap">
<style>
  :root {
    --backdrop: #e9e6e2;
    --card-white: #ffffff;
    --card-black: #141414;
    --brand-blue: #1157b0;
    --ink: #1d1d1d;
    --pattern-dark: #1b1b1b;
    --pattern-light: #2e2e2e;
  }
  * { margin: 0; padding: 0; box-sizing: border-box; }
  html, body {
    width: 1200px; height: 834px; overflow: hidden;
    background: var(--backdrop);
    font-family: "Open Sans", Arial, sans-serif;
  }
  .stage {
    position: relative; width: 1200px; height: 834px;
    display: flex; align-items: center; justify-content: center; gap: 40px;
  }
  .card {
    position: relative; width: 520px; height: 300px;
    border-radius: 26px; overflow: hidden;
    box-shadow: 0 10px 26px rgba(0,0,0,.18);
  }
  .card-front { background: var(--card-white); }
  .card-front .swoosh { position: absolute; inset: 0; }

  .identity { position: absolute; left: 0; top: 38px; padding-left: 44px; z-index: 1; }
  .identity-marker {
    position: absolute; left: 18px; top: 4px; width: 16px; height: 22px;
    background: var(--brand-blue);
  }
  .person-name {
    font-size: 25px; font-weight: 700; color: var(--brand-blue); line-height: 1.1;
    white-space: nowrap;
  }
  .person-title { font-size: 13px; color: var(--ink); margin-top: 2px; white-space: nowrap; }

  .contact-list {
    position: absolute; left: 26px; top: 118px; list-style: none;
    font-size: 13.5px; color: var(--ink); line-height: 1.55; z-index: 1;
  }
  .contact-list li { display: flex; align-items: center; gap: 8px; white-space: nowrap; }
  .contact-icon { width: 12px; height: 12px; fill: var(--brand-blue); flex: none; }

  .brand-name {
    position: absolute; right: 22px; top: 70px;
    font-size: 22px; font-weight: 700; letter-spacing: 3px; color: var(--brand-blue);
    white-space: nowrap; line-height: 1.2;
  }

  .address {
    position: absolute; right: 26px; bottom: 14px; text-align: right;
    font-size: 13.5px; color: var(--ink); line-height: 1.35; white-space: nowrap;
  }

  .card-back { background: var(--card-black); }
  .back-pattern {
    position: absolute; inset: 0;
    background: linear-gradient(135deg, var(--pattern-light) 0%, var(--pattern-dark) 55%, #101010 100%);
  }
  .back-brand {
    position: absolute; inset: 0; display: flex; align-items: center; justify-content: center;
    font-size: 46px; font-weight: 700; letter-spacing: 8px; color: var(--brand-blue);
    white-space: nowrap;
  }
</style>
</head>
<body>
<main class="stage">
  <section class="card card-front" aria-label="Business card front">
    <svg class="swoosh" viewBox="0 0 520 300" aria-hidden="true">
      <path d="M230,0 C290,0 300,140 360,190 C400,222 450,230 520,232 L520,0 Z" fill="var(--brand-blue)"/>
      <path d="M250,0 C310,0 318,132 376,178 C412,206 458,214 520,216 L520,0 Z" fill="var(--card-black)"/>
    </svg>

    <div class="identity">
      <span class="identity-marker"></span>
      <h1 class="person-name">Dana Whitfield</h1>
      <p class="person-title">Managing Director</p>
    </div>

    <ul class="contact-list">
      <li><svg class="contact-icon" viewBox="0 0 12 12"><path d="M3 1 L5 3.5 L4 5 C4.8 6.6 5.6 7.4 7 8 L8.5 7 L11 9 L9.5 11 C5 10.5 1.5 7 1 2.5 Z"/></svg>123 456 789</li>
      <li><svg class="contact-icon" viewBox="0 0 12 12"><rect x="2" y="1" width="8" height="10" rx="1"/></svg>123 456 789</li>
      <li><svg class="contact-icon" viewBox="0 0 12 12"><path d="M1 3 H11 V10 H1 Z M1 3 L6 7 L11 3" stroke="#fff" stroke-width=".8"/></svg>info@youremail.com</li>
      <li><svg class="contact-icon" viewBox="0 0 12 12"><circle cx="6" cy="6" r="5"/></svg>www.yourwebsite.com</li>
    </ul>

    <div class="brand-name">TA BRAMLEY</div>

    <p class="address">Your address, City<br>State, Zip 1234</p>
  </section>

  <section class="card card-back" aria-label="Business card back">
    <div class="back-pattern" role="img" aria-label="Dark embossed repeating brand pattern"></div>
    <div class="back-brand">TA BRAMLEY</div>
  </section>
</main>
</body>
</html>
```